Consulting business card

*1) An Overview:* The business is simply a financial transaction wherein I
offer to provide advice to financial holders of commercial real estate
mortgages (which are sub-performing or non-performing), and said holders
are desirous of selling said mortgages which I will offer advice to said
holders in the purchase of said mortgages. Please note the attached copy
of a proposed line-by-line business card which starts with the 1st line
"RKW Advisory, LLC" with the 2nd line "Purchase of Commercial Mortgage
Loan" and the 3rd line "Sub-performing and Non-performing" is my desired
copy subject to any suggested changes. Please ignore the the copy below
the aforementioned proposed card/copy as it will be activated at a later
date.and advise
*2) The Target Market:* I contact and advise senior officers in banks,
insurance companies, and financial institutions such as CEOs, CFOs, COOs,
and Loan Mitigation Officers: the senior officers are tasked with the
removal of sub-performing and non-performing commercial real estate loans
from their real estate portfolios. The desired market is targeted at $1-10
million USD and located in the US.
*3) Design Specifics: *STYLE should be conservative and be representative
of the financial market contacts; COLOR might show a rich forest green
element, a gold foil accent, and subtle black printing, however,
alternatively, silver foil accent(s) with strong black print would seem in
harmony with the services offered, however, I would appreciate any artful
suggestions; IMAGERY should be subtle (no logo can be strong enough to make
an immediate impact): the quality should make the recipient feel he/she has
just met an experienced and competent financial adviser (I have over 55
years of successful financial and business experience).
720.217.6154davidfredrickjones@gmail.com

```html
<!DOCTYPE html>
<html lang="en">
<head>
<meta charset="utf-8">
<title>RKW Advisory – Business Card</title>
<link href="https://fonts.googleapis.com/css2?family=Tinos:wght@400;700&display=swap" rel="stylesheet">
<style>
  :root {
    --forest: #1f5a24;
    --forest-deep: #173f1c;
    --gold-light: #f3e28a;
    --gold: #d9b84a;
    --ink: #1b1b1b;
    --card: #fbfbfa;
    --backdrop: #e9e6e0;
  }
  * { margin: 0; padding: 0; box-sizing: border-box; }
  html, body {
    width: 1200px; height: 800px; overflow: hidden;
    background: var(--backdrop);
  }
  .canvas {
    width: 1200px; height: 800px;
    display: flex; align-items: center; justify-content: center;
  }
  .business-card {
    position: relative;
    width: 900px; height: 514px;
    background: var(--card);
    border-radius: 16px;
    overflow: hidden;
    box-shadow: 0 6px 22px rgba(0,0,0,0.12);
    font-family: "Tinos", "Times New Roman", serif;
  }
  .card-swoosh { position: absolute; inset: 0; width: 100%; height: 100%; }
  .company-block {
    position: absolute; top: 38px; left: 0; right: 0;
    text-align: center;
  }
  .company-name {
    color: var(--forest);
    font-weight: 700;
    font-size: 39px;
    letter-spacing: 0.5px;
    line-height: 1.1;
  }
  .company-service {
    color: var(--ink);
    font-size: 25px;
    line-height: 38px;
    margin-top: 4px;
  }
  .contact-name {
    position: absolute; left: 92px; top: 232px;
    color: var(--forest);
    font-weight: 700;
    font-size: 31px;
  }
  .contact-list {
    position: absolute; left: 88px; top: 334px;
    list-style: none;
  }
  .contact-item {
    display: flex; align-items: center;
    height: 38px;
    color: var(--ink);
    font-size: 26px;
  }
  .contact-icon { width: 18px; height: 18px; margin-right: 26px; flex: none; }
</style>
</head>
<body>
<main class="canvas">
  <article class="business-card">
    <svg class="card-swoosh" viewBox="0 0 900 514" preserveAspectRatio="none" aria-hidden="true">
      <defs>
        <linearGradient id="gold-band" x1="0" y1="0" x2="1" y2="0">
          <stop offset="0" stop-color="#f6e79a"/>
          <stop offset="0.6" stop-color="#e8cf6a"/>
          <stop offset="1" stop-color="#d4b24a"/>
        </linearGradient>
        <linearGradient id="forest-band" x1="0" y1="1" x2="1" y2="0">
          <stop offset="0" stop-color="#1f4d22"/>
          <stop offset="1" stop-color="#163a1a"/>
        </linearGradient>
      </defs>
      <path d="M0 498 Q520 505 900 288 L900 304 Q700 462 400 514 L0 514 Z" fill="url(#gold-band)"/>
      <path d="M400 514 Q700 462 900 304 L900 514 Z" fill="url(#forest-band)"/>
    </svg>

    <header class="company-block">
      <h1 class="company-name">RKW Advisory</h1>
      <p class="company-service">Purchase of Commercial Mortgage Loan</p>
      <p class="company-service">Sub-performing and Non-performing</p>
    </header>

    <h2 class="contact-name">Elena Marsh</h2>

    <ul class="contact-list">
      <li class="contact-item">
        <svg class="contact-icon" viewBox="0 0 18 18" aria-hidden="true">
          <rect width="18" height="18" fill="var(--forest)"/>
          <rect x="5.5" y="2.5" width="7" height="13" rx="1" fill="#fff"/>
          <rect x="6.8" y="4" width="4.4" height="7" fill="var(--forest)"/>
        </svg>
        <span>555.304.8827</span>
      </li>
      <li class="contact-item">
        <svg class="contact-icon" viewBox="0 0 18 18" aria-hidden="true">
          <rect width="18" height="18" fill="var(--forest)"/>
          <rect x="3" y="5" width="12" height="8" fill="#fff"/>
          <path d="M3 5 L9 10 L15 5" fill="none" stroke="var(--forest)" stroke-width="1.2"/>
        </svg>
        <span>tomasheraldwick@mailbox.example</span>
      </li>
    </ul>
  </article>
</main>
</body>
</html>
```